New Business Card for our Indoor Golf Training Facility

We are looking for designs for a new business card for our indoor golf training facility. Attached is our logo, our logo with our slogan, and here is our elevator pitch (What makes us different from the others) not sure if all the info will fit on one card, maybe you can condense the elevator pitch? here is the info

Elevator Pitch
We work with serious golfers and those that want to be serious golfers…
to make you better, faster, at all phases of the game…
We use the same state-of-the-art technology as professional golfers…
which produces data sets that shows your improvement in real time.
Our facility is available 24/7 to our members, which allows you to improve on your time.

our website: www.birchpinlinks.com

Target Market(s)

Golfers

Font styles to use
Serif
Sans Serif

Colors
ec1f27
f59195
fbd4d5
919191
d3d3d3
1b1b1b

Requirements
Must have
• our logo or our logo with the slogan, elevator pitch (can be condensed or shortened)

```html
<!DOCTYPE html>
<html lang="en">
<head>
<meta charset="utf-8">
<title>Birch Pin Links – Business Card</title>
<link rel="stylesheet" href="https://fonts.googleapis.com/css2?family=Open+Sans:wght@400;600;700&display=swap">
<style>
  :root {
    --brand-red: #ec1f27;
    --card-red: #ec3d36;
    --pink-mid: #f59195;
    --pink-light: #fbd4d5;
    --grey-mid: #919191;
    --grey-light: #d3d3d3;
    --ink: #1b1b1b;
    --paper: #ffffff;
    --backdrop: #e9e7e5;
  }
  * { box-sizing: border-box; margin: 0; padding: 0; }
  html, body {
    width: 1200px; height: 844px; overflow: hidden;
    background: var(--backdrop);
    font-family: "Open Sans", Arial, sans-serif;
  }
  .stage {
    position: relative; width: 1200px; height: 844px;
    display: flex; align-items: center; justify-content: center; gap: 50px;
  }
  .card {
    position: relative; width: 525px; height: 300px; overflow: hidden;
    border-radius: 3px;
    box-shadow: 0 6px 18px rgba(0,0,0,.18);
  }
  .card-front { background: var(--paper); color: var(--ink); }
  .card-back { background: var(--card-red); color: var(--paper); }

  .brand {
    position: absolute; right: 40px; top: 58px; text-align: right;
  }
  .brand-name {
    font-size: 34px; font-weight: 700; color: var(--brand-red); line-height: 1;
    letter-spacing: -0.5px;
  }
  .brand-tagline {
    margin-top: 6px;
    font-size: 11.5px; color: var(--grey-mid); letter-spacing: .2px;
  }

  .contact { position: absolute; left: 38px; bottom: 34px; line-height: 1.28; font-size: 15px; }
  .contact-name { color: var(--brand-red); font-size: 18px; font-weight: 400; }
  .contact-title { color: var(--ink); font-size: 15px; }
  .contact-row { display: flex; align-items: center; gap: 5px; }
  .contact-row svg { width: 13px; height: 13px; flex: none; }
  .contact-address { margin-top: 6px; }

  .pitch { position: absolute; left: 34px; top: 48px; right: 40px; font-size: 12.2px; line-height: 1.42; }
  .pitch-heading { font-size: 15px; font-weight: 700; letter-spacing: .4px; margin-bottom: 10px; }
  .pitch p { margin-bottom: 8px; }
  .pitch-cta { margin-top: 12px; font-size: 13px; }
  .pitch-cta strong { font-size: 16px; font-weight: 700; }
</style>
</head>
<body>
<main class="stage">

  <section class="card card-front" aria-label="Business card front">
    <div class="brand">
      <div class="brand-name">Birch Pin Links</div>
      <div class="brand-tagline">Train Indoors. Play Sharper Outdoors.</div>
    </div>

    <div class="contact">
      <div class="contact-name">Daniel Hart</div>
      <div class="contact-title">Managing Director</div>
      <div class="contact-row">
        <svg viewBox="0 0 14 14" aria-hidden="true">
          <circle cx="7" cy="7" r="6" fill="none" stroke="var(--brand-red)" stroke-width="1.4"/>
          <path d="M4.6 4.2c.4-.4.8-.4 1 0l.6 1c.2.3.1.6-.2.8l-.3.2c.3.8.9 1.4 1.7 1.7l.2-.3c.2-.3.5-.4.8-.2l1 .6c.4.2.4.6 0 1-.7.7-1.6.7-2.6.1-1-.6-1.9-1.5-2.5-2.5-.5-1-.5-1.8.3-2.4z" fill="var(--brand-red)"/>
        </svg>
        <span>555-302-1180</span>
      </div>
      <div class="contact-row">
        <svg viewBox="0 0 14 14" aria-hidden="true">
          <circle cx="7" cy="7" r="6.5" fill="var(--brand-red)"/>
          <circle cx="7" cy="7" r="3.6" fill="none" stroke="#fff" stroke-width="1.2"/>
          <path d="M3.4 7h7.2M7 3.4v7.2" stroke="#fff" stroke-width="0.9"/>
        </svg>
        <span>www.birchpinlinks.com</span>
      </div>
      <div class="contact-address">
        1480 Maple Ridge Dr. Unit B4<br>
        Fairview, OH 45000
      </div>
    </div>
  </section>

  <section class="card card-back" aria-label="Business card back">
    <div class="pitch">
      <h2 class="pitch-heading">ELEVATOR PITCH</h2>
      <p>We work with serious golfers and those that want to be serious golfers… to make you better, faster, at all phases of the game…</p>
      <p>We use the same state-of-the-art technology as professional golfers… which produces data sets that shows your improvement in real time.</p>
      <p>Our facility is available 24/7 to our members, which allows you to improve on your time.</p>
      <div class="pitch-cta">Visit <strong>www.birchpinlinks.com</strong> for more details.</div>
    </div>
  </section>

</main>
</body>
</html>
```